Modern HomePage Design for Church

We are looking for a modern homepage design using the sections we put together in the template. The colors we want are blue, black, grey, and white. We do not want use the colors in the logo. Please modify the logo color to match the website color scheme.

Target Market(s)

Church

Industry/Entity Type

Church

Number of Pages Required

1 page

Colors
0293ce
ffffff
474747
9d9d9d

```html
<!DOCTYPE html>
<html lang="en">
<head>
<meta charset="utf-8">
<title>Riverstone Grace Church — Home</title>
<link href="https://fonts.googleapis.com/css2?family=Lato:wght@300;400;700;900&display=swap" rel="stylesheet">
<style>
:root{
  --blue:#1e5aa8;
  --blue-bright:#0293ce;
  --ink:#1b1b1b;
  --dark:#161616;
  --grey:#474747;
  --mid:#9d9d9d;
  --light:#f0f0f0;
  --white:#ffffff;
}
*{box-sizing:border-box;margin:0;padding:0}
html,body{width:1200px;height:5325px;overflow:hidden}
body{font-family:'Lato',Arial,sans-serif;color:var(--grey);background:var(--white);position:relative}
.abs{position:absolute}
.ph{position:absolute}
.btn{position:absolute;display:flex;align-items:center;justify-content:center;gap:8px;border-radius:30px;font-weight:700;font-size:13px;letter-spacing:.5px;color:var(--white);background:var(--blue);text-transform:uppercase;white-space:nowrap}
.btn .dot{width:14px;height:14px;border-radius:50%;background:var(--white);display:inline-block;position:relative}
.btn .dot::after{content:"";position:absolute;left:5px;top:4px;border-left:5px solid var(--blue);border-top:3px solid transparent;border-bottom:3px solid transparent}
.small{font-size:13px;line-height:22px;color:var(--mid)}
.h-section{position:absolute;left:0;width:1200px;text-align:center;font-weight:900;font-size:40px;color:var(--ink);text-transform:uppercase}

/* nav */
.nav{position:absolute;top:0;left:0;width:1200px;height:43px;background:var(--dark)}
.nav ul{position:absolute;left:140px;top:0;display:flex;gap:22px;list-style:none;height:43px;align-items:center}
.nav li{color:var(--white);font-size:12px;font-weight:700;text-transform:uppercase}
.nav .give{position:absolute;left:902px;top:0;width:153px;height:43px;background:var(--blue);color:var(--white);font-weight:700;font-size:14px;display:flex;align-items:center;justify-content:center}

/* hero */
.hero{top:43px;left:0;width:1200px;height:622px;background:linear-gradient(180deg,#e9e6e2 0%,#cfc6bd 45%,#8a6a4e 75%,#6b4e37 100%)}
.brand{position:absolute;left:140px;top:120px;font-size:30px;font-weight:900;color:var(--blue);text-transform:uppercase;line-height:30px}
.brand small{display:block;font-size:11px;font-weight:700;letter-spacing:1px}
.worship{position:absolute;top:100px;height:36px;border-radius:18px;font-size:12px;font-weight:700;color:var(--white);display:flex;align-items:center;justify-content:center;text-transform:uppercase}
.hero-title{position:absolute;left:0;top:245px;width:1200px;text-align:center;color:var(--white);font-size:70px;font-weight:400;line-height:74px;text-transform:uppercase;letter-spacing:2px}
.hero-sub{position:absolute;left:0;top:405px;width:1200px;text-align:center;color:var(--white);font-size:20px}
.dots{position:absolute;left:555px;top:612px;display:flex;gap:8px}
.dots i{width:10px;height:10px;border-radius:50%;background:var(--white);opacity:.7}
.dots i:first-child{opacity:1;background:var(--blue)}

/* news */
.news{top:665px;left:0;width:1200px;height:60px;background:var(--light)}
.news .label{position:absolute;left:0;top:0;width:280px;height:60px;background:var(--blue);color:var(--white);font-weight:700;font-size:20px;display:flex;align-items:center;padding-left:135px;clip-path:polygon(0 0,260px 0,280px 50%,260px 100%,0 100%)}
.news p{position:absolute;left:315px;top:20px;font-size:14px;color:var(--grey)}
.arrow{position:absolute;top:14px;width:32px;height:32px;border-radius:50%;border:1px solid var(--mid);background:var(--white);display:flex;align-items:center;justify-content:center;font-size:16px;color:var(--ink)}

/* welcome */
.welcome-h{position:absolute;left:140px;top:815px;font-size:40px;font-weight:900;color:var(--ink);text-transform:uppercase}
.welcome-s{position:absolute;left:140px;top:862px;font-size:34px;font-weight:300;color:var(--grey)}
.rule{position:absolute;height:3px;width:45px;background:var(--blue)}
.welcome-p{position:absolute;left:140px;top:955px;width:470px}

/* countdown */
.count{top:1367px;left:0;width:1200px;height:255px;background:var(--ink)}
.timer{position:absolute;left:140px;top:45px;display:flex;gap:20px}
.timer div{width:82px;height:82px;border-radius:50%;border:2px solid var(--white);color:var(--white);text-align:center;padding-top:14px;font-size:30px;font-weight:700;line-height:32px}
.timer small{display:block;font-size:10px;font-weight:400;line-height:12px}
.timer b{color:var(--white);font-size:28px;align-self:center}
.meet{position:absolute;left:685px;top:40px;color:var(--white);text-transform:uppercase;font-size:46px;line-height:52px}
.meet strong{font-weight:900}
.meet span{display:block;font-weight:300}
.meet-date{position:absolute;left:890px;top:170px;color:var(--white);font-size:16px}

/* cards */
.card{position:absolute;top:1722px;height:308px;border:1px solid #e4e4e4;background:var(--white);text-align:center;padding:0 30px}
.card.lift{box-shadow:0 6px 24px rgba(0,0,0,.18);top:1712px;height:328px}
.card svg{margin-top:40px}
.card h3{font-size:15px;font-weight:900;color:var(--ink);margin:20px 0 12px;text-transform:uppercase}
.card .small{font-size:12px;line-height:19px}
.card a{display:block;color:var(--blue);font-weight:700;font-size:11px;margin-top:16px;text-transform:uppercase}

/* involved */
.tile{position:absolute;width:200px;height:243px}
.tile span{position:absolute;left:0;bottom:14px;background:var(--ink);color:var(--white);font-size:11px;font-weight:700;padding:6px 18px;text-transform:uppercase}
.involve{top:2123px;left:600px;width:600px;height:487px;background:var(--blue);color:var(--white)}
.involve h2{position:absolute;left:150px;top:75px;font-size:44px;font-weight:900;text-transform:uppercase}
.involve .rule{background:var(--white);left:250px;top:140px}
.involve p{position:absolute;left:70px;top:170px;width:460px;text-align:center;font-size:13px;line-height:24px;color:#dbe6f5}
.btn.ghost{background:transparent;border:2px solid var(--white)}
.btn.ghost .dot::after{border-left-color:var(--blue)}

/* blog */
.post{position:absolute;top:2815px;width:280px}
.post .img{height:188px;position:relative}
.badge{position:absolute;left:14px;top:0;width:52px;height:56px;background:var(--blue);color:var(--white);text-align:center;font-weight:900;font-size:18px;padding-top:6px;line-height:20px;clip-path:polygon(0 0,100% 0,100% 100%,50% 85%,0 100%)}
.badge small{display:block;font-size:9px;font-weight:700}
.post h4{font-size:18px;font-weight:700;color:var(--ink);margin:26px 0 12px}
.post .small{font-size:12px;line-height:19px}
.post .btn{position:relative;width:112px;height:38px;margin-top:20px;font-size:11px}

/* pastor */
.pastor{top:3284px;left:0;width:1200px;height:468px;background:linear-gradient(180deg,#2b2a2c,#1a191b 60%,#232124)}
.pastor h2{position:absolute;top:85px;color:var(--white);font-size:32px;font-weight:900;text-transform:uppercase}
.quote{position:absolute;left:395px;top:185px;color:var(--white);font-size:30px;font-weight:700;line-height:36px}
.play{position:absolute;left:760px;width:64px;height:62px;border:1px solid #555;background:#111;display:flex;align-items:center;justify-content:center}
.pod{position:absolute;left:850px;color:var(--white);font-size:16px;font-weight:700}

/* events */
.event{position:absolute;left:175px;width:850px;height:213px;border:2px solid #e4e4e4;background:var(--white)}
.event .img{position:absolute;top:28px;width:245px;height:157px}
.event h4{position:absolute;top:40px;width:360px;font-size:17px;font-weight:700;line-height:24px;color:var(--ink)}
.meta{position:absolute;width:360px;font-size:11px;color:var(--grey);line-height:22px}
.meta svg{vertical-align:-2px;margin-right:6px}
.event .btn{width:112px;height:38px;font-size:11px}

/* footer */
.foot-brand{position:absolute;left:0;top:4770px;width:1200px;text-align:center;font-size:18px;font-weight:900;color:var(--blue);text-transform:uppercase}
.footer{top:4845px;left:0;width:1200px;height:480px}
.footer h5{position:absolute;top:68px;color:var(--white);font-size:18px;font-weight:900;text-transform:uppercase}
.fitem{position:absolute;width:250px;height:70px}
.fitem .thumb{position:absolute;left:0;top:0;width:85px;height:62px}
.fitem b{position:absolute;left:100px;top:4px;color:var(--white);font-size:13px}
.fitem p{position:absolute;left:100px;top:24px;width:150px;font-size:10px;line-height:15px;color:var(--mid)}
.tag{position:absolute;height:26px;border-radius:13px;background:#3a3a3a;color:#cfcfcf;font-size:11px;display:flex;align-items:center;justify-content:center}
.social{position:absolute;top:380px;left:510px;display:flex;gap:14px}
.social i{width:30px;height:30px;border-radius:50%;border:1px solid #888;display:block}
.legal{position:absolute;top:435px;font-size:11px;color:var(--mid)}
</style>
</head>
<body>

<header class="nav">
  <ul><li>Home</li><li>Team</li><li>Features</li><li>Events</li><li>Sermons</li><li>Contact</li><li>Blog</li></ul>
  <div class="give">GIVE ONLINE</div>
</header>

<section class="ph hero" role="img" aria-label="Photo of a small wooden church model on a table in soft light">
  <div class="brand">Riverstone<small>Grace Church</small></div>
  <div class="worship" style="left:640px;width:185px;background:var(--blue)">Sunday Worship 10:15</div>
  <div class="worship" style="left:848px;width:205px;background:var(--grey)">Sunday Worship 10:15</div>
  <h1 class="hero-title">Riverstone<br>Grace Church</h1>
  <p class="hero-sub">Lorem Ipsum is simply dummy text of the printing industry</p>
  <div class="btn" style="left:505px;top:452px;width:190px;height:44px;background:#3a2e26">Get Started <span class="dot"></span></div>
  <div class="dots"><i></i><i></i><i></i><i></i><i></i><i></i></div>
</section>

<section class="abs news">
  <div class="label">Latest News</div>
  <p>Lorem Ipsum is simply dummy text of the printing and typesetting industry</p>
  <div class="arrow" style="left:885px">&#8592;</div>
  <div class="arrow" style="left:930px">&#8594;</div>
</section>

<section class="welcome">
  <h2 class="welcome-h">Welcome to</h2>
  <p class="welcome-s">Riverstone Grace Church</p>
  <div class="rule" style="left:140px;top:922px"></div>
  <div class="welcome-p small">
    <p>Sed ut perspiciatis unde omnis iste natus error sit voluptatem accusantium doloremque laudantium, totam rem aperiam, eaque ipsa quae ab illo inventore veritatis et quasi architecto beatae vitae dicta sunt explicabo.</p>
    <p style="margin-top:16px">Nemo enim ipsam voluptatem quia voluptas sit aspernatur aut odit aut fugit, sed quia consequuntur magni dolores eos qui ratione voluptatem sequi nesciunt. Neque porro quisquam est, qui dolorem ipsum quia dolor sit amet, consectetur, adipisci velit, sed quia non numquam eius modi tempora incidunt ut labore.</p>
  </div>
  <div class="btn" style="left:140px;top:1205px;width:190px;height:50px">Get Started <span class="dot"></span></div>
  <div class="ph" role="img" aria-label="Photo of a smiling woman and a pastor holding a bible" style="left:615px;top:745px;width:560px;height:622px;background:linear-gradient(160deg,#ffffff 0%,#eef3f8 40%,#c9d3de 100%)"></div>
</section>

<section class="abs count">
  <div class="timer">
    <div>06<small>Days</small></div><b>:</b>
    <div>04<small>Hours</small></div><b>:</b>
    <div>30<small>Minutes</small></div><b>:</b>
    <div>45<small>Secs</small></div>
  </div>
  <div class="btn" style="left:280px;top:160px;width:155px;height:40px">Read More</div>
  <div class="meet"><strong>Church Leaders</strong><span>Meeting</span></div>
  <div class="meet-date">Apr 05,2019 10:00am</div>
</section>

<section class="services">
  <div class="card" style="left:145px;width:285px">
    <svg width="60" height="60" viewBox="0 0 60 60"><circle cx="30" cy="30" r="28" fill="#eef1f5"/><path d="M22 44V26a3 3 0 0 1 6 0v-8a3 3 0 0 1 6 0v8a3 3 0 0 1 6 0v12c0 4-3 6-7 6z" fill="none" stroke="#1b1b1b" stroke-width="2.5"/></svg>
    <h3>What We Believe?</h3>
    <p class="small">Sed ut perspiciatis unde omnis iste natus error sit voluptatem accusantium dolor remque lauon totam rem aperiam.</p>
    <a>Read More</a>
  </div>
  <div class="card lift" style="left:458px;width:285px">
    <svg width="60" height="60" viewBox="0 0 60 60"><circle cx="30" cy="30" r="28" fill="#eef1f5"/><circle cx="30" cy="30" r="15" fill="none" stroke="#1b1b1b" stroke-width="2.5"/><ellipse cx="30" cy="30" rx="6" ry="15" fill="none" stroke="#1b1b1b" stroke-width="2"/><path d="M15 30h30" stroke="#1b1b1b" stroke-width="2"/></svg>
    <h3>Services &amp; Location</h3>
    <p class="small">Sed ut perspiciatis unde omnis iste natus error sit voluptatem accusantium dolor remque lauon totam rem aperiam.</p>
    <a>Browse More</a>
  </div>
  <div class="card" style="left:770px;width:285px">
    <svg width="60" height="60" viewBox="0 0 60 60"><circle cx="30" cy="30" r="28" fill="#eef1f5"/><circle cx="30" cy="24" r="10" fill="none" stroke="#1b1b1b" stroke-width="2.5"/><path d="M30 19v10M17 44h26M20 38h20" stroke="#1b1b1b" stroke-width="2.5"/></svg>
    <h3>Giving</h3>
    <p class="small">Sed ut perspiciatis unde omnis iste natus error sit voluptatem accusantium dolor remque lauon totam rem aperiam.</p>
    <a>Read More</a>
  </div>
</section>

<section class="involved">
  <div class="tile" role="img" aria-label="Photo of church members praying together" style="left:0;top:2123px;background:linear-gradient(160deg,#6b4a3a,#3a2a24)"><span>Sed ut perspiciatis</span></div>
  <div class="tile" role="img" aria-label="Photo of a group gathered in fellowship" style="left:200px;top:2123px;background:linear-gradient(160deg,#4d4a52,#2b2a30)"><span>Sed ut perspiciatis</span></div>
  <div class="tile" role="img" aria-label="Photo of a worship leader speaking" style="left:400px;top:2123px;background:linear-gradient(160deg,#7a4b3c,#402a24)"><span>Sed ut perspiciatis</span></div>
  <div class="tile" role="img" aria-label="Photo of volunteers serving a meal" style="left:0;top:2366px;background:linear-gradient(160deg,#5a4036,#2e2220)"><span>Sed ut perspiciatis</span></div>
  <div class="tile" role="img" aria-label="Photo of hands joined in a circle" style="left:200px;top:2366px;background:linear-gradient(160deg,#6a5346,#34271f)"></div>
  <div class="tile" role="img" aria-label="Photo of a bible study group" style="left:400px;top:2366px;background:linear-gradient(160deg,#4a3f3a,#241f1d)"><span>Sed ut perspiciatis</span></div>
  <div class="abs involve">
    <h2>Get Involved</h2>
    <div class="rule"></div>
    <p>Sed ut perspiciatis unde omnis iste natus error sit voluptatem accusantium doloremque laudantium, totam rem aperiam, eaque ipsa quae ab illo inventore veritatis et quasi architecto beatae vitae dicta sunt explicabo.</p>
    <div class="btn ghost" style="left:210px;top:345px;width:180px;height:48px">Get Started <span class="dot"></span></div>
  </div>
</section>

<section class="blog">
  <h2 class="h-section" style="top:2700px">Blog Posts</h2>
  <div class="rule" style="left:578px;top:2762px"></div>
  <article class="post" style="left:145px">
    <div class="img" role="img" aria-label="Photo of hands clasped in prayer" style="background:linear-gradient(160deg,#5b6f86,#2c3a4a)"><div class="badge">05<small>APR</small></div></div>
    <h4>Sed ut perspiciatis unde antium</h4>
    <p class="small">Sed ut perspiciatis unde omnis iste natus error sit voluptatem accusantium doloremque laudantium, totam rem aperiam.</p>
    <div class="btn">Read More</div>
  </article>
  <article class="post" style="left:460px">
    <div class="img" role="img" aria-label="Photo of a worship concert with raised hands" style="background:linear-gradient(160deg,#3a6fb8,#101a3a)"><div class="badge">05<small>APR</small></div></div>
    <h4>Sed ut perspiciatis unde antium</h4>
    <p class="small">Sed ut perspiciatis unde omnis iste natus error sit voluptatem accusantium doloremque laudantium, totam rem aperiam.</p>
    <div class="btn">Read More</div>
  </article>
  <article class="post" style="left:775px">
    <div class="img" role="img" aria-label="Photo of many hands stacked together" style="background:linear-gradient(160deg,#6b5a4e,#2d2520)"><div class="badge">05<small>APR</small></div></div>
    <h4>Sed ut perspiciatis unde antium</h4>
    <p class="small">Sed ut perspiciatis unde omnis iste natus error sit voluptatem accusantium doloremque laudantium, totam rem aperiam.</p>
    <div class="btn">Read More</div>
  </article>
</section>

<section class="abs pastor" role="img" aria-label="Dark photo background of a congregation">
  <h2 style="left:215px">Pastor</h2>
  <div class="rule" style="left:240px;top:132px"></div>
  <div class="ph" role="img" aria-label="Portrait photo of the pastor" style="left:145px;top:175px;width:225px;height:200px;background:linear-gradient(160deg,#8a6a58,#3d2e27)"></div>
  <p class="quote">“ One thing I ask<br>&nbsp;&nbsp;of the Lord ”</p>
  <p class="small" style="position:absolute;left:415px;top:270px;width:240px;color:#bdbdbd;font-size:12px;line-height:19px">Sed ut perspiciatis unde omnis iste natus error sit voluptatem accusantium doloremque laudantium, totam rem aperiam.</p>
  <h2 style="left:835px">Podcasts</h2>
  <div class="rule" style="left:870px;top:132px"></div>
  <div class="play" style="top:170px"><svg width="20" height="22"><path d="M2 1l17 10L2 21z" fill="#fff"/></svg></div>
  <div class="pod" style="top:178px">Ut enim ad minima veniam</div>
  <div class="play" style="top:255px"><svg width="20" height="22"><path d="M2 1l17 10L2 21z" fill="#fff"/></svg></div>
  <div class="pod" style="top:268px">Sed ut perspiciatis</div>
  <div class="play" style="top:340px"><svg width="20" height="22"><path d="M2 1l17 10L2 21z" fill="#fff"/></svg></div>
  <div class="pod" style="top:352px">Quis autem vel reprehenderit</div>
</section>

<section class="events">
  <h2 class="h-section" style="top:3838px">Upcoming Events</h2>
  <div class="rule" style="left:578px;top:3898px"></div>
  <p class="small" style="position:absolute;left:0;top:3918px;width:1200px;text-align:center">Sed ut perspiciatis unde omnis iste natus error</p>

  <div class="event" style="top:3983px">
    <div class="img" role="img" aria-label="Photo of people in a church service" style="left:20px;background:linear-gradient(160deg,#5a4a40,#2a221e)"></div>
    <div class="badge" style="left:-10px;top:-14px">05<small>APR</small></div>
    <h4 style="left:295px">Quis autem vel eum iure reprehenderit qui in ea voluptate velit esse quam nihil</h4>
    <div class="meta" style="left:295px;top:108px">
      <div><svg width="11" height="11"><rect x="1" y="2" width="9" height="8" fill="none" stroke="#1e5aa8"/></svg>Friday,10:00am - Friday,7:00pm</div>
      <div><svg width="11" height="11"><circle cx="5.5" cy="4.5" r="3.5" fill="#1e5aa8"/></svg>Ashgrove Chapel</div>
      <div><svg width="11" height="11"><path d="M1 6l3 3 6-7" stroke="#1e5aa8" fill="none" stroke-width="1.5"/></svg>Ut enim ad minima veniam, quis nostrum</div>
    </div>
    <div class="btn" style="left:695px;top:117px">Read More</div>
  </div>

  <div class="event" style="top:4232px">
    <h4 style="left:40px">Quis autem vel eum iure reprehenderit qui in ea voluptate velit esse quam nihil</h4>
    <div class="meta" style="left:40px;top:108px">
      <div><svg width="11" height="11"><rect x="1" y="2" width="9" height="8" fill="none" stroke="#1e5aa8"/></svg>Friday,10:00am - Friday,7:00pm</div>
      <div><svg width="11" height="11"><circle cx="5.5" cy="4.5" r="3.5" fill="#1e5aa8"/></svg>Ashgrove Chapel</div>
      <div><svg width="11" height="11"><path d="M1 6l3 3 6-7" stroke="#1e5aa8" fill="none" stroke-width="1.5"/></svg>Ut enim ad minima veniam, quis nostrum</div>
    </div>
    <div class="btn" style="left:385px;top:117px">Read More</div>
    <div class="img" role="img" aria-label="Photo of hands joined around a table" style="left:585px;background:linear-gradient(160deg,#6d5a4c,#30261f)"></div>
    <div class="badge" style="left:806px;top:-14px">05<small>APR</small></div>
  </div>

  <div class="event" style="top:4480px">
    <div class="img" role="img" aria-label="Photo of a congregation singing" style="left:20px;background:linear-gradient(160deg,#5d4b42,#2b231f)"></div>
    <div class="badge" style="left:-10px;top:-14px">05<small>APR</small></div>
    <h4 style="left:295px">Quis autem vel eum iure reprehenderit qui in ea voluptate velit esse quam nihil</h4>
    <div class="meta" style="left:295px;top:108px">
      <div><svg width="11" height="11"><rect x="1" y="2" width="9" height="8" fill="none" stroke="#1e5aa8"/></svg>Friday,10:00am - Friday,7:00pm</div>
      <div><svg width="11" height="11"><circle cx="5.5" cy="4.5" r="3.5" fill="#1e5aa8"/></svg>Ashgrove Chapel</div>
      <div><svg width="11" height="11"><path d="M1 6l3 3 6-7" stroke="#1e5aa8" fill="none" stroke-width="1.5"/></svg>Ut enim ad minima veniam, quis nostrum</div>
    </div>
    <div class="btn" style="left:695px;top:117px">Read More</div>
  </div>
</section>

<div class="foot-brand">Riverstone Grace</div>

<footer class="abs footer">
  <svg class="abs" style="left:0;top:0" width="1200" height="480" viewBox="0 0 1200 480"><path d="M0 40 Q600 -30 1200 40 V480 H0Z" fill="#161616"/></svg>
  <h5 style="left:140px">Latest Sermons</h5>
  <div class="fitem" style="left:140px;top:115px"><div class="thumb" role="img" aria-label="Sermon photo" style="background:linear-gradient(160deg,#6b5446,#2e241e)"></div><b>Quis autem vel eum iure</b><p>Quis autem vel eum iure reprehenderit voluptate velit esse.</p></div>
  <div class="fitem" style="left:140px;top:205px"><div class="thumb" role="img" aria-label="Sermon photo" style="background:linear-gradient(160deg,#5a4a42,#28201c)"></div><b>Quis autem vel eum iure</b><p>Quis autem vel eum iure reprehenderit voluptate velit esse.</p></div>
  <h5 style="left:490px">Sermon Tags</h5>
  <div class="tag" style="left:490px;top:115px;width:60px">Faith</div>
  <div class="tag" style="left:565px;top:115px;width:85px">Forgiveness</div>
  <div class="tag" style="left:490px;top:150px;width:70px">Holiness</div>
  <div class="tag" style="left:575px;top:150px;width:55px">Lead</div>
  <div class="tag" style="left:490px;top:185px;width:60px">Prayer</div>
  <div class="tag" style="left:565px;top:185px;width:95px">Understanding</div>
  <div class="ph" role="img" aria-label="Photo of silhouetted people joining hands" style="left:490px;top:225px;width:210px;height:95px;background:linear-gradient(180deg,#d6e2f0,#5e7fa8)"></div>
  <h5 style="left:765px">Latest News</h5>
  <div class="fitem" style="left:765px;top:115px"><div class="thumb" role="img" aria-label="News photo" style="background:linear-gradient(160deg,#6b5446,#2e241e)"></div><b>Quis autem vel eum iure</b><p>Quis autem vel eum iure reprehenderit voluptate velit esse.</p></div>
  <div class="fitem" style="left:765px;top:205px"><div class="thumb" role="img" aria-label="News photo" style="background:linear-gradient(160deg,#5a4a42,#28201c)"></div><b>Quis autem vel eum iure</b><p>Quis autem vel eum iure reprehenderit voluptate velit esse.</p></div>
  <div class="social"><i></i><i></i><i></i><i></i><i></i></div>
  <div class="legal" style="left:140px">Copyright © 2019. Riverstone Grace All rights reserved</div>
  <div class="legal" style="left:850px">Terms and conditions &nbsp;|&nbsp; Privacy policy</div>
</footer>

</body>
</html>
```